Core values in our company OKV (Residency and Relocation)

Do good:
1. Being Direct and communicative for the benefit of all parties
2. Working for the Benefit of the company, client and team members
3. Wanting to improve to create a better impact
4. Having healthy rivalry
Be ahead of curve:
1. Having the confidence to break through barriers which arise
2. Desire to grow and learn towards establishment and agreed goal
3. Getting off the sidelines and get into the game
4. Keeping the end game in mind having due regard to processes and milestones
5. Self starter and works on own initiative
6. Diligent and impactful in your field of responsibility
Truth and Honesty
2. Have the confidence and ability to speak what you really want to communicate
3. Being truthful to yourself, clients and colleagues to find the innovations that lie within
4. Seeking the truth by opening things up for discussion
5. Being Optimistic
Background Information on our Company:OKV is a professional law firm in London Docklands. We caters for both private and corporate clients ranging from highly regarded and established law firms to boutique and niche immigration practices. We also specialises in expert legal advice and prides itself on providing services that go beyond the expectations of its clients.
What we need: We need a Poster about Truth and Honesty, this is to show one of our values as a company. It will need to be vibrant and straight to the point. Colours can be orange grey white and yellow. Attached is our company logo.
Reason: To remind colleagues that this is one of our main values and it is instilled in our company.
Things we would like:
1. To create a point of focus
2. Use shapes to create visual interest
3. Use creative illustrations
4. Take the viewer’s focus on a journey with clever perspective
Industry/Entity Type
Legal
Requirements
Must have
- a globe (Picture)
- Do good:
- 1. Being Direct and communicative for the benefit of all parties
- 2. Working for the Benefit of the company, client and team members
- 3. Wanting to improve to create a better impact
- 4. Having healthy rivalry
- Be ahead of curve:
- 1. Having the confidence to break through barriers which arise
- 2. Desire to grow and learn towards establishment and agreed goal
- 3. Getting off the sidelines and get into the game
- 4. Keeping the end game in mind having due regard to processes and milestones
- 5. Self starter and works on own initiative
- 6. Diligent and impactful in your field of responsibility
- Truth and Honesty
- 2. Have the confidence and ability to speak what you really want to communicate
- 3. Being truthful to yourself, clients and colleagues to find the innovations that lie within
- 4. Seeking the truth by opening things up for discussion
- 5. Being Optimistic

```html
<!DOCTYPE html>
<html lang="en">
<head>
<meta charset="utf-8">
<title>Core Values in OKV</title>
<link rel="stylesheet" href="https://fonts.googleapis.com/css2?family=Libre+Baskerville:wght@400;700&family=Mulish:wght@700;800&display=swap">
<style>
  :root {
    --backdrop: #e4e4e4;
    --navy-deep: #12165a;
    --navy-mid: #1f2a8a;
    --violet: #3a2a7a;
    --orange: #f7891f;
    --yellow: #fdbb1c;
    --ink: #2d2d2d;
    --heading-grey: #4a4a4a;
    --panel-light: #fafafa;
    --panel-shade: #e2e2e2;
    --footer-dark: #2e2c2c;
    --footer-brown: #5a3e24;
    --white: #ffffff;
  }
  * { box-sizing: border-box; margin: 0; padding: 0; }
  html, body { width: 1200px; height: 2163px; overflow: hidden; }
  body { background: var(--backdrop); font-family: "Mulish", Arial, sans-serif; }

  .poster {
    position: absolute; left: 40px; top: 289px;
    width: 1120px; height: 1585px;
    background: var(--white); overflow: hidden;
    box-shadow: 0 10px 40px rgba(0,0,0,.25);
  }

  .globe-visual {
    position: absolute; left: 0; top: 0; width: 1120px; height: 676px;
    background:
      radial-gradient(circle at 52% 62%, #2f4fc4 0%, var(--navy-mid) 28%, var(--navy-deep) 55%, transparent 56%),
      linear-gradient(160deg, var(--violet) 0%, #1c1f6e 55%, #10145a 100%);
  }

  .top-rule {
    position: absolute; left: 440px; top: 0; width: 680px; height: 8px;
    background: var(--orange);
  }

  .brand-tab {
    position: absolute; left: 0; top: 0; width: 451px; height: 214px;
    background: linear-gradient(180deg, #ffffff 0%, #e6e6e6 100%);
    border-right: 6px solid var(--orange); border-bottom: 6px solid var(--orange);
    border-bottom-right-radius: 60px;
  }
  .brand-name {
    position: absolute; left: 92px; top: 28px;
    font-family: "Mulish", Arial, sans-serif; font-weight: 800;
    font-size: 96px; line-height: 1; color: var(--ink); letter-spacing: 2px;
  }
  .brand-mark {
    position: absolute; left: 50px; top: 52px; width: 28px; height: 28px;
    border-radius: 50%; background: var(--orange);
  }
  .brand-line {
    position: absolute; left: 92px; top: 136px;
    font-family: "Libre Baskerville", Georgia, serif; font-size: 19px; color: var(--ink);
  }

  .values-panel { position: absolute; left: 0; top: 676px; width: 620px; height: 797px; }

  .title {
    position: absolute; left: 36px; top: 780px;
    font-family: "Libre Baskerville", Georgia, serif; color: var(--heading-grey);
    text-transform: uppercase; line-height: 1;
  }
  .title .small { display: block; font-size: 52px; font-weight: 400; letter-spacing: -1px; }
  .title .big { display: block; font-size: 96px; font-weight: 700; margin-top: 8px; letter-spacing: -2px; }

  .value-tab {
    position: absolute; height: 60px; width: 356px;
    background: linear-gradient(90deg, var(--orange) 0%, var(--yellow) 100%);
    border-radius: 0 30px 30px 0;
    font-family: "Libre Baskerville", Georgia, serif; font-weight: 700;
    font-size: 24px; color: var(--ink);
    display: flex; align-items: center; padding-left: 36px;
    box-shadow: 0 8px 10px -6px rgba(0,0,0,.35);
  }
  .value-tab.truth { left: 0; top: 1004px; }
  .value-tab.good { left: 486px; top: 714px; }
  .value-tab.ahead { left: 486px; top: 1025px; }

  .value-list { position: absolute; list-style: none; }
  .value-list li {
    position: relative; padding-left: 46px;
    font-size: 19.5px; font-weight: 800; line-height: 1.12; color: var(--ink);
  }
  .value-list li svg { position: absolute; left: 0; top: 2px; width: 22px; height: 22px; }

  .value-list.truth { left: 36px; top: 1102px; width: 440px; }
  .value-list.truth li { margin-bottom: 34px; text-align: justify; }
  .value-list.good { left: 522px; top: 804px; width: 580px; }
  .value-list.good li { margin-bottom: 22px; }
  .value-list.ahead { left: 522px; top: 1116px; width: 580px; }
  .value-list.ahead li { margin-bottom: 22px; }

  .footer-bar {
    position: absolute; left: 0; top: 1473px; width: 1120px; height: 112px;
    background: linear-gradient(90deg, var(--footer-brown) 0%, var(--footer-dark) 45%, var(--footer-dark) 100%);
    border-top: 6px solid var(--orange);
    display: flex; align-items: center; justify-content: flex-end; padding-right: 28px;
  }
  .web-address {
    font-family: "Libre Baskerville", Georgia, serif; font-weight: 700;
    font-size: 26px; color: var(--white); display: flex; align-items: center; gap: 14px;
  }
  .web-address svg { width: 26px; height: 26px; }
</style>
</head>
<body>
<main class="poster">
  <div class="globe-visual" role="img" aria-label="Dotted blue globe with connection arcs linking cities across the world"></div>
  <div class="top-rule"></div>

  <div class="brand-tab">
    <span class="brand-mark"></span>
    <span class="brand-name">OKV</span>
    <span class="brand-line">residency and relocation</span>
  </div>

  <svg class="values-panel" viewBox="0 0 620 797" aria-hidden="true">
    <defs>
      <linearGradient id="panelShade" x1="0" y1="0" x2="1" y2="0">
        <stop offset="0" stop-color="#e4e4e4"/>
        <stop offset="0.5" stop-color="#f7f7f7"/>
        <stop offset="1" stop-color="#ececec"/>
      </linearGradient>
    </defs>
    <path d="M0 0 H486 V560 C486 700 520 770 600 797 H0 Z" fill="url(#panelShade)"/>
    <path d="M486 0 V560 C486 700 520 770 600 797" fill="none" stroke="#cfcfcf" stroke-width="3"/>
  </svg>

  <h1 class="title"><span class="small">Core Values</span><span class="big">In OKV</span></h1>

  <div class="value-tab truth">Truth and Honesty</div>
  <ul class="value-list truth">
    <li><svg viewBox="0 0 22 22"><circle cx="11" cy="11" r="9" fill="none" stroke="#f7891f" stroke-width="2"/><path d="M6.5 11.5l3 3 6-6.5" fill="none" stroke="#f7891f" stroke-width="2.2"/></svg>Having the confidence to break through barriers which arise</li>
    <li><svg viewBox="0 0 22 22"><circle cx="11" cy="11" r="9" fill="none" stroke="#f7891f" stroke-width="2"/><path d="M6.5 11.5l3 3 6-6.5" fill="none" stroke="#f7891f" stroke-width="2.2"/></svg>Have the confidence and ability to speak what you really want to communicate</li>
    <li><svg viewBox="0 0 22 22"><circle cx="11" cy="11" r="9" fill="none" stroke="#f7891f" stroke-width="2"/><path d="M6.5 11.5l3 3 6-6.5" fill="none" stroke="#f7891f" stroke-width="2.2"/></svg>Being truthful to yourself, clients and colleagues to find the innovations that lie within</li>
    <li><svg viewBox="0 0 22 22"><circle cx="11" cy="11" r="9" fill="none" stroke="#f7891f" stroke-width="2"/><path d="M6.5 11.5l3 3 6-6.5" fill="none" stroke="#f7891f" stroke-width="2.2"/></svg>Seeking the truth by opening things up for discussion</li>
    <li><svg viewBox="0 0 22 22"><circle cx="11" cy="11" r="9" fill="none" stroke="#f7891f" stroke-width="2"/><path d="M6.5 11.5l3 3 6-6.5" fill="none" stroke="#f7891f" stroke-width="2.2"/></svg>Being Optimistic</li>
  </ul>

  <div class="value-tab good">Do good:</div>
  <ul class="value-list good">
    <li><svg viewBox="0 0 22 22"><circle cx="11" cy="11" r="9" fill="none" stroke="#f7891f" stroke-width="2"/><path d="M6.5 11.5l3 3 6-6.5" fill="none" stroke="#f7891f" stroke-width="2.2"/></svg>Being Direct and communicative for the<br>benefit of all parties</li>
    <li><svg viewBox="0 0 22 22"><circle cx="11" cy="11" r="9" fill="none" stroke="#f7891f" stroke-width="2"/><path d="M6.5 11.5l3 3 6-6.5" fill="none" stroke="#f7891f" stroke-width="2.2"/></svg>Working for the Benefit of the company, client<br>and team members</li>
    <li><svg viewBox="0 0 22 22"><circle cx="11" cy="11" r="9" fill="none" stroke="#f7891f" stroke-width="2"/><path d="M6.5 11.5l3 3 6-6.5" fill="none" stroke="#f7891f" stroke-width="2.2"/></svg>Wanting to improve to create a better impact</li>
    <li><svg viewBox="0 0 22 22"><circle cx="11" cy="11" r="9" fill="none" stroke="#f7891f" stroke-width="2"/><path d="M6.5 11.5l3 3 6-6.5" fill="none" stroke="#f7891f" stroke-width="2.2"/></svg>Having healthy rivalry</li>
  </ul>

  <div class="value-tab ahead">Be ahead of curve:</div>
  <ul class="value-list ahead">
    <li><svg viewBox="0 0 22 22"><circle cx="11" cy="11" r="9" fill="none" stroke="#f7891f" stroke-width="2"/><path d="M6.5 11.5l3 3 6-6.5" fill="none" stroke="#f7891f" stroke-width="2.2"/></svg>Having the confidence to break through<br>barriers which arise</li>
    <li><svg viewBox="0 0 22 22"><circle cx="11" cy="11" r="9" fill="none" stroke="#f7891f" stroke-width="2"/><path d="M6.5 11.5l3 3 6-6.5" fill="none" stroke="#f7891f" stroke-width="2.2"/></svg>Desire to grow and learn towards establishment<br>and agreed goal</li>
    <li><svg viewBox="0 0 22 22"><circle cx="11" cy="11" r="9" fill="none" stroke="#f7891f" stroke-width="2"/><path d="M6.5 11.5l3 3 6-6.5" fill="none" stroke="#f7891f" stroke-width="2.2"/></svg>Getting off the sidelines and get into the game</li>
    <li><svg viewBox="0 0 22 22"><circle cx="11" cy="11" r="9" fill="none" stroke="#f7891f" stroke-width="2"/><path d="M6.5 11.5l3 3 6-6.5" fill="none" stroke="#f7891f" stroke-width="2.2"/></svg>Keeping the end game in mind having due<br>regard to processes and milestones</li>
    <li><svg viewBox="0 0 22 22"><circle cx="11" cy="11" r="9" fill="none" stroke="#f7891f" stroke-width="2"/><path d="M6.5 11.5l3 3 6-6.5" fill="none" stroke="#f7891f" stroke-width="2.2"/></svg>Self starter and works on own initiative</li>
    <li><svg viewBox="0 0 22 22"><circle cx="11" cy="11" r="9" fill="none" stroke="#f7891f" stroke-width="2"/><path d="M6.5 11.5l3 3 6-6.5" fill="none" stroke="#f7891f" stroke-width="2.2"/></svg>Diligent and impactful in your field of responsibility</li>
  </ul>

  <footer class="footer-bar">
    <span class="web-address">
      <svg viewBox="0 0 26 26" aria-hidden="true"><circle cx="13" cy="13" r="11" fill="none" stroke="#f7891f" stroke-width="2"/><ellipse cx="13" cy="13" rx="5" ry="11" fill="none" stroke="#f7891f" stroke-width="1.6"/><path d="M2 13h22M4 7.5h18M4 18.5h18" stroke="#f7891f" stroke-width="1.4"/></svg>
      www.okvresidency.com
    </span>
  </footer>
</main>
</body>
</html>
```